HOT TUB - SPAS service needs an business card

I need an business for my company who his specialise in a maintenance,water treatment and cleaning of Hot Tub - Spas for commercial and residential customers. The company operate mainly in the ski resort of Chamonix, Megève and St Gervais. The final product should communicate pure water, cleanest and professional for luxury property's.
I have upload a logo but any improvement on it is welcome.(color,size, details etc..) or any other idea. Thank you
Company Name: 58 BAINS
My name: Lucien Marchetti
Email: lucimarch@examplemail.net
Tel: +33 (0)6 71 58 29 64
Description to be on the card in french(first langage) and in English:
- Spas service
- Entretien, traitement eau, nettoyage.
- Maintenance, water treatment, cleaning.
Industry/Entity Type
Residential
Colors
Designer to choose colors to be used in the design.
Look and feel
Each slider illustrates characteristics of the customer's brand and the style your logo design should communicate.

```html
<!DOCTYPE html>
<html lang="fr">
<head>
<meta charset="utf-8">
<title>58 BAINS – Business Card</title>
<link rel="stylesheet" href="https://fonts.googleapis.com/css2?family=Source+Sans+3:wght@400;600&display=swap">
<style>
  :root {
    --page-bg: #eef1f4;
    --front-blue: #1fa5fb;
    --back-blue: #0b78d9;
    --ink: #ffffff;
    --ink-soft: rgba(255, 255, 255, 0.92);
  }
  * { margin: 0; padding: 0; box-sizing: border-box; }
  html, body {
    width: 1200px;
    height: 935px;
    overflow: hidden;
    background: var(--page-bg);
    font-family: "Source Sans 3", "Myriad Pro", sans-serif;
    color: var(--ink);
  }
  .canvas { position: relative; width: 1200px; height: 935px; }

  .card { position: absolute; width: 740px; height: 424px; }
  .card--front { left: 37px; top: 42px; background: var(--front-blue); }
  .card--back  { left: 298px; top: 487px; background: var(--back-blue); }

  .company-name {
    position: absolute; left: 36px; top: 162px;
    font-size: 38px; font-weight: 600; letter-spacing: 0.3px;
  }
  .contact {
    position: absolute; left: 38px;
    display: flex; align-items: center; gap: 10px;
    font-size: 25px; font-weight: 400;
  }
  .contact--phone { top: 235px; }
  .contact--email { top: 278px; }
  .contact svg { width: 22px; height: 22px; flex: none; }

  .owner-name {
    position: absolute; right: 39px; top: 240px;
    font-size: 32px; font-weight: 600;
  }
  .services {
    position: absolute; left: 38px; top: 348px;
    font-size: 24px; line-height: 31px; color: var(--ink-soft);
  }

  .brand-block {
    position: absolute; left: 0; right: 0; top: 125px;
    display: flex; justify-content: center; align-items: center; gap: 16px;
  }
  .brand-block__square { width: 22px; height: 22px; background: var(--ink); }
  .brand-block__name { font-size: 56px; font-weight: 600; letter-spacing: 1px; }

  .services-title {
    position: absolute; left: 0; right: 0; top: 294px;
    text-align: center; font-size: 28px; font-weight: 600;
  }
  .services-list {
    position: absolute; left: 0; right: 0;
    text-align: center; font-size: 27px; font-weight: 400;
  }
  .services-list--fr { top: 336px; }
  .services-list--en { top: 372px; }
  .services-list span + span { margin-left: 12px; }
  .services-list span::before { content: "•"; margin-right: 3px; }
</style>
</head>
<body>
<main class="canvas">

  <section class="card card--front" aria-label="Recto de la carte">
    <h1 class="company-name">58 BAINS</h1>

    <p class="contact contact--phone">
      <svg viewBox="0 0 24 24" aria-hidden="true">
        <circle cx="12" cy="12" r="10.5" fill="none" stroke="#fff" stroke-width="1.6"/>
        <path d="M8.5 6.5c-1 1-1.2 3 .5 6s3.8 4.8 5.5 5c1 .1 1.7-.4 2-1l-2-2-1.3.8c-1-.5-2.4-2.2-2.8-3.3l.9-1.2-1.3-2.6z" fill="#fff"/>
      </svg>
      +33 (0)6 71 58 29 64
    </p>
    <p class="contact contact--email">
      <svg viewBox="0 0 24 24" aria-hidden="true">
        <path d="M2 10l10-6 10 6v10H2z" fill="#fff"/>
        <path d="M3 11l9 5.5 9-5.5" fill="none" stroke="#1fa5fb" stroke-width="1.6"/>
      </svg>
      lucimarch@examplemail.net
    </p>

    <p class="owner-name">Lucien Marchetti</p>

    <p class="services">
      Entretien, traitement eau, nettoyage<br>
      Maintenance, water treatment, cleaning.
    </p>
  </section>

  <section class="card card--back" aria-label="Verso de la carte">
    <div class="brand-block">
      <span class="brand-block__square" aria-hidden="true"></span>
      <span class="brand-block__name">58 BAINS</span>
    </div>

    <h2 class="services-title">SPAS SERVICES</h2>
    <p class="services-list services-list--fr">
      <span>Entretien</span><span>traitement eau</span><span>nettoyage</span>
    </p>
    <p class="services-list services-list--en">
      <span>Maintenance</span><span>water treatment</span><span>cleaning.</span>
    </p>
  </section>

</main>
</body>
</html>
```